Carpet cleaning company focused on high quality needs business cards

We are a growing company that just merged with another company and need to design a new business card. We do both residential as well as commercial cleaning. We do carpet, tile & grout, upholstery, hard floors, and stain & pet odor removal. We treat our customers like family and strive to achieve outstanding results with every job.

```html
<!DOCTYPE html>
<html lang="en">
<head>
<meta charset="utf-8">
<title>Northpine Steam Care – Business Cards</title>
<link href="https://fonts.googleapis.com/css2?family=Open+Sans:wght@400;600;800&display=swap" rel="stylesheet">
<style>
  :root {
    --stage: #222222;
    --brand-red: #ef4a42;
    --ink: #111111;
    --paper: #ffffff;
    --muted: #222222;
  }
  * { box-sizing: border-box; margin: 0; padding: 0; }
  html, body {
    width: 1200px; height: 780px; overflow: hidden;
    background: var(--stage);
    font-family: "Open Sans", Arial, sans-serif;
  }
  .canvas { position: relative; width: 1200px; height: 780px; }
  .card {
    position: absolute; width: 520px; height: 297px; overflow: hidden;
    box-shadow: 0 10px 24px rgba(0,0,0,0.55);
  }
  /* Front */
  .card--front { left: 60px; top: 60px; background: var(--brand-red); }
  .brand {
    position: absolute; display: flex; align-items: center; gap: 14px;
  }
  .brand__square { width: 64px; height: 64px; flex: none; }
  .brand__name {
    font-weight: 800; color: var(--ink); line-height: 1.02;
    text-transform: uppercase; letter-spacing: -0.5px;
  }
  .card--front .brand { left: 120px; top: 106px; }
  .card--front .brand__square { background: var(--paper); width: 84px; height: 84px; }
  .card--front .brand__name { font-size: 27px; }

  /* Back */
  .card--back { left: 620px; top: 423px; background: var(--paper); }
  .edge-band { position: absolute; background: var(--brand-red); width: 12px; }
  .edge-band--left { left: 0; top: 118px; bottom: 0; }
  .edge-band--right { right: 0; top: 34px; height: 130px; }
  .card--back .brand { left: 34px; top: 104px; }
  .card--back .brand__square { background: var(--brand-red); width: 60px; height: 60px; }
  .card--back .brand__name { font-size: 19px; }
  .divider {
    position: absolute; left: 272px; top: 58px; width: 1.5px; height: 150px;
    background: var(--ink); transform: rotate(-8deg);
  }
  .contact { position: absolute; left: 300px; top: 56px; }
  .contact__name { font-size: 22px; font-weight: 800; color: var(--ink); letter-spacing: 0.2px; }
  .contact__name .first { color: var(--brand-red); }
  .contact__title { font-size: 12px; font-weight: 600; color: var(--muted); margin-top: 1px; }
  .contact__list { list-style: none; margin-top: 18px; }
  .contact__list li {
    display: flex; align-items: center; gap: 8px;
    font-size: 12.5px; color: var(--muted); margin-bottom: 5px;
  }
  .contact__list svg { width: 13px; height: 13px; flex: none; fill: var(--brand-red); }
  .address {
    position: absolute; left: 0; right: 0; bottom: 38px; text-align: center;
    font-size: 13.5px; color: var(--ink); padding-left: 80px;
  }
</style>
</head>
<body>
<main class="canvas">
  <section class="card card--front" aria-label="Card front">
    <div class="brand">
      <span class="brand__square"></span>
      <span class="brand__name">Northpine<br>Steam Care</span>
    </div>
  </section>

  <section class="card card--back" aria-label="Card back">
    <span class="edge-band edge-band--left"></span>
    <span class="edge-band edge-band--right"></span>

    <div class="brand">
      <span class="brand__square"></span>
      <span class="brand__name">Northpine<br>Steam Care</span>
    </div>

    <span class="divider"></span>

    <div class="contact">
      <p class="contact__name"><span class="first">Marta</span> Kovalenko</p>
      <p class="contact__title">Managing Director</p>
      <ul class="contact__list">
        <li>
          <svg viewBox="0 0 24 24" aria-hidden="true"><path d="M6.6 10.8a15.1 15.1 0 0 0 6.6 6.6l2.2-2.2a1 1 0 0 1 1-.25 11.4 11.4 0 0 0 3.6.57 1 1 0 0 1 1 1V20a1 1 0 0 1-1 1A17 17 0 0 1 3 4a1 1 0 0 1 1-1h3.5a1 1 0 0 1 1 1 11.4 11.4 0 0 0 .57 3.6 1 1 0 0 1-.25 1z"/></svg>
          (555) 014-2290
        </li>
        <li>
          <svg viewBox="0 0 24 24" aria-hidden="true"><path d="M2 5h20v14H2zm2 2v.5l8 5 8-5V7zm0 2.8V17h16V9.8l-8 5z"/></svg>
          hello@northpinesteam.com
        </li>
        <li>
          <svg viewBox="0 0 24 24" aria-hidden="true"><circle cx="12" cy="12" r="10"/></svg>
          www.northpinesteam.com
        </li>
      </ul>
    </div>

    <p class="address">412 Harlow Ave Brookfield, Texas 75990 USA</p>
  </section>
</main>
</body>
</html>
```